Help design website for "Brightwater Civic Advisors" to advance the common good

Here is the Google doc link that lays out the design:

https://files.plumrivet.example/sheet/d/7QmTzR2wLx9KpVbN4hJcY8sEaUoFdG3iXkMnPq5rWt6/edit?usp=sharing

Here is the Google drive folder with the logos and photos: https://vault.plumrivet.example/open?id=4HkWp9LzQe2TxRvN8mBaYc3DsUoJfG6

The testimonials are being gathered and will be shared by Friday, 1/4.

The winner will also have to migrate the coding files to my hosting site.

Thank you for your help! Looking forward to seeing your designs.

Target Market(s)

Prospective clients

Industry/Entity Type

Non Profit

Coding

Coded - Design and coding required

Number of Pages Required

5+ page

Requirements
Must have
• Noted in the Google doc regarding layout.
Nice to have

```html
<!DOCTYPE html>
<html lang="en">
<head>
<meta charset="utf-8">
<title>Brightwater Civic Advisors — Contact</title>
<link rel="stylesheet" href="https://fonts.googleapis.com/css2?family=Poppins:wght@500;600;700&family=Open+Sans:wght@400;600&display=swap">
<style>
  :root {
    --brand-blue: #3d8bce;
    --ink: #141414;
    --body-text: #2a2a2a;
    --field-border: #b9b9b9;
    --footer-bg: #272830;
    --footer-rule: #4a4b55;
    --white: #ffffff;
  }
  * { box-sizing: border-box; margin: 0; padding: 0; }
  html, body { width: 1174px; height: 1200px; overflow: hidden; background: var(--white); }
  body { position: relative; font-family: "Open Sans", Arial, sans-serif; color: var(--body-text); }

  /* Header */
  .site-header { position: absolute; left: 0; top: 0; width: 1174px; height: 122px; background: var(--brand-blue); }
  .brand-name {
    position: absolute; font-family: "Poppins", Arial, sans-serif; font-weight: 600;
    color: var(--white); line-height: 1; white-space: nowrap; letter-spacing: 0;
  }
  .site-header .brand-name { left: 141px; top: 48px; font-size: 22px; }
  .cta-button {
    position: absolute; left: 720px; top: 20px; width: 313px; height: 40px;
    border: 2px solid var(--white); color: var(--white);
    font-family: "Poppins", Arial, sans-serif; font-weight: 600; font-size: 13px;
    display: flex; align-items: center; justify-content: center; text-decoration: none;
  }
  .main-nav a {
    position: absolute; top: 86px; color: var(--white); text-decoration: none;
    font-family: "Poppins", Arial, sans-serif; font-weight: 600; font-size: 13px;
  }
  .main-nav .nav-about { left: 550px; }
  .main-nav .nav-services { left: 627px; }
  .main-nav .nav-media { left: 825px; }
  .main-nav .nav-contact { left: 968px; padding-bottom: 2px; border-bottom: 1.5px solid var(--white); padding-right: 6px; }

  /* Content */
  .section-title { position: absolute; left: 0; width: 1174px; text-align: center; font-family: "Poppins", Arial, sans-serif; font-weight: 600; color: var(--ink); }
  .rates-title { top: 180px; font-size: 29px; }
  .consult-title { top: 345px; font-size: 24px; }
  .lead { position: absolute; text-align: center; font-size: 14.4px; line-height: 20px; color: var(--body-text); }
  .rates-lead { left: 387px; width: 400px; top: 235px; }
  .consult-lead { left: 287px; width: 600px; top: 394px; }

  .contact-form .field {
    position: absolute; border: 1.5px solid var(--field-border); border-radius: 3px;
    padding: 13px 0 0 19px; font-size: 11.5px; color: #2f2f2f; text-transform: uppercase; background: var(--white);
  }
  .f-first { left: 268px; top: 482px; width: 316px; height: 43px; }
  .f-last { left: 600px; top: 482px; width: 316px; height: 43px; }
  .f-org { left: 268px; top: 534px; width: 316px; height: 43px; }
  .f-email { left: 600px; top: 534px; width: 316px; height: 43px; }
  .f-subject { left: 268px; top: 587px; width: 647px; height: 43px; }
  .f-message { left: 268px; top: 640px; width: 647px; height: 98px; }
  .submit-button {
    position: absolute; left: 530px; top: 766px; width: 120px; height: 40px;
    background: var(--brand-blue); color: var(--white); border: none;
    font-family: "Poppins", Arial, sans-serif; font-weight: 700; font-size: 16px;
    display: flex; align-items: center; justify-content: center;
  }

  /* Footer */
  .site-footer { position: absolute; left: 0; top: 888px; width: 1174px; height: 312px; }
  .footer-shape { position: absolute; left: 0; top: 0; }
  .site-footer .brand-name { left: 141px; top: 180px; font-size: 28px; }
  .footer-divider { position: absolute; left: 598px; top: 125px; width: 1px; height: 139px; background: var(--footer-rule); }
  .footer-heading { position: absolute; left: 656px; top: 142px; color: var(--white); font-weight: 600; font-size: 11.5px; }
  .footer-menu { position: absolute; left: 656px; top: 175px; color: var(--white); font-size: 11.5px; white-space: nowrap; }
  .footer-menu .sep { margin: 0 9px; }
  .copyright { position: absolute; left: 657px; top: 235px; color: var(--white); font-size: 11px; font-family: Arial, sans-serif; }
</style>
</head>
<body>
  <header class="site-header">
    <div class="brand-name">Brightwater Civic Advisors</div>
    <a class="cta-button" href="#consult">BOOK A COMPLIMENTARY CONSULTATION</a>
    <nav class="main-nav">
      <a class="nav-about" href="#">ABOUT</a>
      <a class="nav-services" href="#">SERVICES &amp; TESTIMONIALS</a>
      <a class="nav-media" href="#">MEDIA &amp; IMPACT</a>
      <a class="nav-contact" href="#">CONTACT</a>
    </nav>
  </header>

  <main>
    <h1 class="section-title rates-title">RATES</h1>
    <p class="lead rates-lead">Depending on the services requested, Dana offers an hourly rate, a package rate, or a retainer fee based on the scope and complexity of the project.</p>

    <h2 class="section-title consult-title" id="consult">Book a complimentary consultation</h2>
    <p class="lead consult-lead">Use the form below to tell Dana about your inquiry, and she will schedule a 30-minute meeting, phone call, or video chat to discuss your project outcomes.</p>

    <form class="contact-form">
      <div class="field f-first">First Name</div>
      <div class="field f-last">Last Name</div>
      <div class="field f-org">Organization Name</div>
      <div class="field f-email">Email Address</div>
      <div class="field f-subject">Subject</div>
      <div class="field f-message">Message</div>
      <div class="submit-button">SUBMIT</div>
    </form>
  </main>

  <footer class="site-footer">
    <svg class="footer-shape" width="1174" height="312" viewBox="0 0 1174 312" aria-hidden="true">
      <polygon points="0,104 585,0 1174,104 1174,312 0,312" fill="var(--footer-bg)"/>
    </svg>
    <div class="brand-name">Brightwater Civic Advisors</div>
    <div class="footer-divider"></div>
    <div class="footer-heading">MENU</div>
    <div class="footer-menu">ABOUT<span class="sep">|</span>SERVICES &amp; TESTIMONIALS<span class="sep">|</span>MEDIA &amp; IMPACT<span class="sep">|</span>CONTACT</div>
    <div class="copyright">Copyrights @ 2019 All Rights Reserved</div>
  </footer>
</body>
</html>
```